Ridgeline Journeys business card

please see website
www.ridgelinejourneys.comau

info needed on card
Curtis Halvey
Ph
email
Adventure Riding GPS trails

please use my logo and colours off my site

Curtis Halvey
curtis@ridgelinejourneys.com

```html
<!DOCTYPE html>
<html lang="en">
<head>
<meta charset="utf-8">
<title>Ridgeline Journeys – Business Card</title>
<link rel="stylesheet" href="https://fonts.googleapis.com/css2?family=Open+Sans:wght@400;600;700&display=swap">
<style>
  :root {
    --page-bg: #2e2824;
    --card-black: #0d0d0d;
    --card-edge: #1c1c1c;
    --accent-yellow: #f2cd00;
    --text-white: #f2f2f2;
    --text-silver: #c9c9c9;
    --mark-grey: #6e6e6e;
  }
  * { margin: 0; padding: 0; box-sizing: border-box; }
  html, body {
    width: 1200px;
    height: 900px;
    overflow: hidden;
    background: var(--page-bg);
    font-family: "Open Sans", Arial, sans-serif;
  }
  .canvas {
    position: relative;
    width: 1200px;
    height: 900px;
    display: flex;
    align-items: center;
    justify-content: center;
    gap: 50px;
  }
  .card {
    position: relative;
    width: 525px;
    height: 300px;
    background: var(--card-black);
    border: 1px solid var(--card-edge);
    border-radius: 2px;
    box-shadow: 0 14px 30px rgba(0, 0, 0, 0.45);
    overflow: hidden;
  }

  /* Front: contact side */
  .card-front .brand-block {
    position: absolute;
    left: 40px;
    top: 0;
    width: 200px;
    height: 100%;
    display: flex;
    align-items: center;
    gap: 12px;
  }
  .brand-square {
    flex: none;
    width: 22px;
    height: 22px;
    background: var(--accent-yellow);
  }
  .brand-name {
    color: var(--text-white);
    font-weight: 700;
    font-size: 22px;
    line-height: 1.15;
  }
  .divider {
    position: absolute;
    left: 262px;
    top: 70px;
    width: 1px;
    height: 160px;
    background: linear-gradient(to bottom, transparent, var(--accent-yellow) 50%, transparent);
    opacity: 0.7;
  }
  .contact {
    position: absolute;
    left: 285px;
    top: 96px;
  }
  .contact-name {
    color: var(--accent-yellow);
    font-weight: 600;
    font-size: 19px;
    margin-bottom: 8px;
  }
  .contact-list { list-style: none; }
  .contact-item {
    display: flex;
    align-items: center;
    gap: 8px;
    color: var(--text-white);
    font-size: 13.5px;
    line-height: 24px;
  }
  .contact-icon { width: 12px; height: 12px; flex: none; }

  /* Back: brand side */
  .card-back {
    display: flex;
    flex-direction: column;
    align-items: center;
    justify-content: center;
    gap: 30px;
  }
  .back-brand {
    display: flex;
    align-items: center;
    gap: 16px;
  }
  .back-brand .brand-square {
    width: 28px;
    height: 28px;
    background: var(--text-silver);
  }
  .back-brand .brand-name {
    color: var(--text-silver);
    font-size: 30px;
  }
  .tagline {
    color: var(--text-silver);
    font-weight: 600;
    font-size: 14px;
    letter-spacing: 0.2px;
  }
</style>
</head>
<body>
<main class="canvas">

  <section class="card card-front" aria-label="Business card front">
    <div class="brand-block">
      <span class="brand-square"></span>
      <span class="brand-name">Ridgeline Journeys</span>
    </div>
    <div class="divider"></div>
    <div class="contact">
      <p class="contact-name">Curtis Halvey</p>
      <ul class="contact-list">
        <li class="contact-item">
          <svg class="contact-icon" viewBox="0 0 12 12" aria-hidden="true"><path fill="#f2cd00" d="M1 3.5C1 2 2 1.5 6 1.5S11 2 11 3.5L9 4.5 8 3H4L3 4.5ZM3 5.5h6l1.5 5h-9Z"/></svg>
          044-987 650 312
        </li>
        <li class="contact-item">
          <svg class="contact-icon" viewBox="0 0 12 12" aria-hidden="true"><rect x="1" y="2.5" width="10" height="7" fill="#f2cd00"/><path d="M1 2.5l5 4 5-4" fill="none" stroke="#0d0d0d" stroke-width="1"/></svg>
          curtis@ridgelinejourneys.com
        </li>
        <li class="contact-item">
          <svg class="contact-icon" viewBox="0 0 12 12" aria-hidden="true"><g fill="none" stroke="#f2cd00" stroke-width="1.6"><rect x="1" y="5" width="6" height="3.5" rx="1.7" transform="rotate(-45 4 6.7)"/><rect x="5" y="3.5" width="6" height="3.5" rx="1.7" transform="rotate(-45 8 5.2)"/></g></svg>
          www.ridgelinejourneys.comau
        </li>
      </ul>
    </div>
  </section>

  <section class="card card-back" aria-label="Business card back">
    <div class="back-brand">
      <span class="brand-square"></span>
      <span class="brand-name">Ridgeline Journeys</span>
    </div>
    <p class="tagline">Adventure Riding GPS trails</p>
  </section>

</main>
</body>
</html>
```